Bright Path Notes Wordpress Blog

I need to design a WordPress blog page. The name of the Blog is "Bright Path Notes". I am hoping for a simple design that is easy for me to post future posts to. I like the color teal for this. The website is brightpathnotesblog.com where I am going to write a personal blog. I don't have a logo for this, but am hoping for a header that has some swirly, but classy looking text. Easy on the eyes. The website will only have a couple of pages - the home landing page, and an about me page.

Font styles to use
Script

Colors
00a990
86cfc6
cfeae6

Requirements
Must have
• A header for the landing page of the blog. Clean layout of where the blog posts will lie.

```html
<!DOCTYPE html>
<html lang="en">
<head>
<meta charset="utf-8">
<title>Bright Path Notes</title>
<link href="https://fonts.googleapis.com/css2?family=Great+Vibes&family=Lato:ital,wght@0,400;0,700;0,900;1,400&family=Open+Sans:wght@400;600;700&display=swap" rel="stylesheet">
<style>
:root{
  --teal:#17909c;
  --teal-dark:#0f7a85;
  --teal-soft:#86cfc6;
  --teal-pale:#cfeae6;
  --ink:#1d1d1d;
  --body:#555;
  --muted:#8a8a8a;
  --line:#e2e2e2;
  --page:#f2f2f2;
  --white:#fff;
  --star:#e5b811;
  --panel:#eef1f2;
}
*{box-sizing:border-box;margin:0;padding:0}
html,body{width:1200px;height:2778px;overflow:hidden}
body{position:relative;background:var(--page);font-family:"Open Sans",Arial,sans-serif;color:var(--body)}
.abs{position:absolute}

/* header */
.site-header{position:absolute;left:0;top:0;width:1200px;height:93px;background:var(--white);z-index:3}
.brand{position:absolute;left:98px;top:14px;display:flex;align-items:center;gap:12px}
.brand-mark{width:14px;height:14px;background:var(--teal)}
.brand-name{font-family:"Great Vibes",cursive;font-weight:400;font-size:46px;line-height:60px;color:var(--ink)}
.main-nav a{position:absolute;top:38px;font-family:"Lato",sans-serif;font-weight:700;font-size:16px;color:#222;text-decoration:none;letter-spacing:.3px}
.main-nav .active{color:var(--teal)}

/* hero */
.hero{position:absolute;left:0;top:93px;width:1200px;height:490px;overflow:hidden}
.hero-photo{position:absolute;inset:0;background:
  radial-gradient(circle at 690px 330px,#fff 0,#f2efe7 40px,rgba(210,205,195,.6) 160px,rgba(0,0,0,0) 320px),
  linear-gradient(100deg,#8e8a83 0%,#b5b0a5 35%,#c9c3b6 55%,#6e5648 72%,#4d3a30 100%)}
.hero-arrow{position:absolute;top:297px;width:42px;height:42px;border:1px solid rgba(255,255,255,.7);background:rgba(255,255,255,.12)}
.hero-copy{position:absolute;left:98px;top:82px;width:460px;color:var(--white)}
.hero-title{font-family:"Lato",sans-serif;font-weight:700;font-size:48px;line-height:56px;text-transform:uppercase;letter-spacing:.5px}
.hero-rule{width:452px;height:2px;background:var(--white);margin:14px 0 18px}
.hero-text{font-size:15px;line-height:23px;color:#f3f3f3;width:460px}
.btn-ghost{display:inline-block;margin-top:30px;width:178px;height:38px;border:2px solid var(--white);border-radius:20px;text-align:center;line-height:34px;font-family:"Lato",sans-serif;font-weight:700;font-size:14px;color:var(--white)}
.hero-wave{position:absolute;left:0;bottom:0}

/* posts */
.post-card{position:absolute;left:98px;width:626px;height:587px;background:var(--white);border:1px solid var(--line)}
.post-title{position:absolute;left:20px;top:18px;font-family:"Lato",sans-serif;font-weight:900;font-size:28px;color:var(--ink);text-transform:uppercase;letter-spacing:.3px}
.post-meta{position:absolute;left:20px;top:64px;font-size:12.5px;color:#666;display:flex;align-items:center;gap:8px}
.post-meta .ic{width:11px;height:11px;border-radius:2px;background:var(--teal);display:inline-block}
.post-meta .sep{color:#aaa;margin:0 6px}
.stars{color:var(--star);letter-spacing:1px;font-size:13px}
.reviews{color:#999}
.post-photo{position:absolute;left:0;top:106px;width:624px;height:286px}
.post-excerpt{position:absolute;left:20px;top:412px;width:584px;font-size:11.6px;line-height:24px;color:#555}
.btn-outline{position:absolute;left:20px;top:527px;width:138px;height:37px;border:1.5px solid #9fb9bd;border-radius:19px;text-align:center;line-height:34px;font-family:"Lato",sans-serif;font-weight:700;font-size:12px;color:var(--teal)}
.share-row{position:absolute;right:28px;top:537px;display:flex;gap:6px;font-size:11px;font-weight:700}
.share-row span{border:1px solid #cfd4d8;background:#f4f6f8;padding:1px 6px;border-radius:2px;color:#3b4a5e}
.share-row .count{background:var(--white);color:#333;font-weight:400}
.view-more{position:absolute;left:624px;top:2510px;font-family:"Lato",sans-serif;font-weight:700;font-size:14px;color:#777}

/* sidebar */
.sidebar{position:absolute;left:756px;top:635px;width:344px;height:1713px;background:var(--white)}
.profile{position:absolute;left:0;top:0;width:344px;height:406px;background:var(--teal);color:var(--white);text-align:center}
.avatar{position:absolute;left:124px;top:20px;width:96px;height:96px;border-radius:50%;border:4px solid var(--white);background:radial-gradient(circle at 50% 40%,#e9d6b9,#b79b74)}
.profile-name{position:absolute;left:0;right:0;top:130px;font-family:"Lato",sans-serif;font-weight:700;font-size:18px}
.profile-role{position:absolute;left:0;right:0;top:160px;font-family:"Lato",sans-serif;font-style:italic;font-size:13px}
.profile-rule{position:absolute;left:16px;right:16px;top:193px;height:1px;background:rgba(255,255,255,.35)}
.profile-bio{position:absolute;left:14px;right:14px;top:210px;font-size:11.4px;line-height:26px}
.profile-social{position:absolute;left:0;right:0;top:339px;display:flex;justify-content:center;gap:18px}
.profile-social span{width:33px;height:33px;border:1px solid rgba(255,255,255,.7);display:flex;align-items:center;justify-content:center}
.profile-social span::after{content:"";width:9px;height:9px;border-radius:50%;background:var(--white)}

.widget-title{position:absolute;left:22px;font-family:"Lato",sans-serif;font-weight:900;font-size:25px;color:var(--ink);text-transform:uppercase;white-space:nowrap}
.related-item{position:absolute;left:22px;width:300px;height:112px;border-bottom:1px solid var(--line)}
.related-thumb{position:absolute;left:0;top:0;width:92px;height:74px;border:3px solid #f0f0f0}
.related-text{position:absolute;left:110px;top:0;width:185px;font-family:"Lato",sans-serif;font-weight:700;font-size:13.5px;line-height:21px;color:#333}
.related-date{position:absolute;left:110px;top:52px;font-size:11.5px;color:#888}
.related-date::before{content:"";display:inline-block;width:9px;height:9px;background:var(--teal);margin-right:5px;border-radius:1px}
.link-teal{position:absolute;left:24px;font-family:"Lato",sans-serif;font-weight:700;font-size:14px;color:var(--teal)}

.newsletter{position:absolute;left:0;top:1047px;width:344px;height:287px;background:var(--panel)}
.email-field{position:absolute;left:14px;top:90px;width:318px;height:43px;background:var(--white);border:1px solid #dde2e4;font-size:11.5px;color:#555;line-height:41px;padding-left:16px}
.btn-solid{position:absolute;left:16px;top:148px;width:314px;height:42px;border-radius:21px;background:var(--teal);color:var(--white);text-align:center;line-height:42px;font-family:"Lato",sans-serif;font-weight:700;font-size:16px}
.newsletter-note{position:absolute;left:20px;top:220px;width:310px;font-size:11.5px;line-height:26px;color:#666}

.fb-card{position:absolute;left:4px;top:1448px;width:336px;height:149px;background:linear-gradient(100deg,#5e5955 0%,#8b857c 45%,#6c5346 75%,#3f3029 100%)}
.fb-brand{position:absolute;left:12px;top:12px;width:74px;height:64px;background:var(--white);display:flex;align-items:center;justify-content:center;font-family:"Lato",sans-serif;font-weight:900;font-size:10px;color:var(--ink);text-align:center;line-height:12px}
.fb-name{position:absolute;left:100px;top:12px;font-family:"Lato",sans-serif;font-weight:700;font-size:15px;color:var(--white);text-transform:uppercase}
.fb-likes{position:absolute;left:100px;top:34px;font-size:12px;color:#eee}
.fb-btn{position:absolute;top:108px;height:28px;background:#f6f7f9;border:1px solid #ccd0d5;font-size:12px;font-weight:700;color:#4b4f56;line-height:26px;padding:0 10px}
.fb-note{position:absolute;left:20px;top:1617px;font-size:11.5px;color:#666}
.fb-friends{position:absolute;left:20px;top:1647px;display:flex;gap:5px}
.fb-friends span{width:39px;height:42px}

/* footer */
.site-footer{position:absolute;left:0;top:2602px;width:1200px;height:176px;background:var(--page);border-top:4px solid var(--teal);text-align:center}
.footer-social{position:absolute;left:0;right:0;top:42px;display:flex;justify-content:center;gap:14px}
.footer-social span{width:16px;height:16px;border-radius:3px;background:#8a8a8a}
.footer-links{position:absolute;left:0;right:0;top:84px;font-size:13px;color:#555}
.footer-links .sep{margin:0 12px;color:#999}
.copyright{position:absolute;left:0;right:0;top:118px;font-size:13px;color:#555}
</style>
</head>
<body>

<header class="site-header">
  <div class="brand"><span class="brand-name">Bright Path Notes</span><span class="brand-mark"></span></div>
  <nav class="main-nav">
    <a class="active" style="left:686px">HOME</a>
    <a style="left:776px">ABOUT MAYA</a>
    <a style="left:926px">CONTACT LINKS</a>
    <svg class="abs" style="left:1088px;top:40px" width="16" height="16" viewBox="0 0 16 16"><circle cx="6.5" cy="6.5" r="4.8" fill="none" stroke="#222" stroke-width="2"/><line x1="10" y1="10" x2="14.5" y2="14.5" stroke="#222" stroke-width="2.4"/></svg>
  </nav>
</header>

<section class="hero">
  <div class="hero-photo" role="img" aria-label="Climber scaling a rugged rock face against a hazy sunlit sky"></div>
  <div class="hero-arrow" style="left:16px"><svg width="40" height="40" viewBox="0 0 40 40"><polyline points="23,13 16,20 23,27" fill="none" stroke="#fff" stroke-width="2"/></svg></div>
  <div class="hero-arrow" style="left:1142px"><svg width="40" height="40" viewBox="0 0 40 40"><polyline points="17,13 24,20 17,27" fill="none" stroke="#fff" stroke-width="2"/></svg></div>
  <div class="hero-copy">
    <h1 class="hero-title">Bright Path<br>Notes</h1>
    <div class="hero-rule"></div>
    <p class="hero-text">At vero eos et accusamus et iusto odio dignissimos dcim us qui blanditiis praesentium voluptatum.</p>
    <span class="btn-ghost">GET MORE INFO &gt;&gt;</span>
  </div>
  <svg class="hero-wave" width="1200" height="90" viewBox="0 0 1200 90">
    <path d="M0 40 C300 -10 520 80 800 50 C960 32 1080 20 1200 22 L1200 90 L0 90Z" fill="#2c6670"/>
    <path d="M0 52 C300 5 520 88 800 60 C960 44 1080 32 1200 34 L1200 90 L0 90Z" fill="#9fd2d4"/>
    <path d="M0 62 C300 20 520 96 800 70 C960 56 1080 44 1200 46 L1200 90 L0 90Z" fill="#e6f1f2"/>
    <path d="M0 72 C300 40 520 100 800 80 C960 68 1080 58 1200 60 L1200 90 L0 90Z" fill="#f2f2f2"/>
  </svg>
</section>

<article class="post-card" style="top:635px">
  <h2 class="post-title">Atvero eos accus iusto odio</h2>
  <div class="post-meta"><span class="ic"></span>16/03/2017<span class="sep">|</span><span class="ic"></span>9:00 Am<span class="sep">|</span><span class="ic"></span>0 comments<span class="sep">|</span><span class="stars">★★★★☆</span><span class="reviews">(34 Reviews)</span></div>
  <div class="post-photo" role="img" aria-label="Person raising arms toward a golden sunset over the sea" style="background:linear-gradient(180deg,#d9a23a 0%,#f3cb5c 40%,#e4a93a 70%,#8a6a3a 100%)"></div>
  <p class="post-excerpt">At vero eos et accusamus et iusto odio dignissimos ducimus qui blanditiis praesentium voluptatum dele niti atque corrupti quos dolores et quas molestias excepturi sint occaecati cupiditate non providentsimil ique sunt in culpa qui officia deserunt mollitia animi, id est laborum et dolorum fuga. Et harum quidem rerum facilis est et expedita distinctio. m soluta nobis est eligend.</p>
  <span class="btn-outline">READ MORE &gt;&gt;</span>
  <div class="share-row"><span>Like</span><span class="count">200</span><span>Share</span><span class="count">200</span><span>+1</span><span class="count">200</span></div>
</article>

<article class="post-card" style="top:1263px">
  <h2 class="post-title">Atvero eos accus iusto odio</h2>
  <div class="post-meta"><span class="ic"></span>16/03/2017<span class="sep">|</span><span class="ic"></span>9:00 Am<span class="sep">|</span><span class="ic"></span>0 comments<span class="sep">|</span><span class="stars">★★★★☆</span><span class="reviews">(34 Reviews)</span></div>
  <div class="post-photo" role="img" aria-label="Handwritten goal-setting checklist on paper beside a red mug on a wooden table" style="background:linear-gradient(100deg,#8a4a2e 0%,#7a5438 30%,#e8e4da 45%,#efebe2 75%,#6b4a32 100%)"></div>
  <p class="post-excerpt">At vero eos et accusamus et iusto odio dignissimos ducimus qui blanditiis praesentium voluptatum dele niti atque corrupti quos dolores et quas molestias excepturi sint occaecati cupiditate non providentsimil ique sunt in culpa qui officia deserunt mollitia animi, id est laborum et dolorum fuga. Et harum quidem rerum facilis est et expedita distinctio. m soluta nobis est eligend.</p>
  <span class="btn-outline">READ MORE &gt;&gt;</span>
  <div class="share-row"><span>Like</span><span class="count">200</span><span>Share</span><span class="count">200</span><span>+1</span><span class="count">200</span></div>
</article>

<article class="post-card" style="top:1896px">
  <h2 class="post-title">Atvero eos accus iusto odio</h2>
  <div class="post-meta"><span class="ic"></span>16/03/2017<span class="sep">|</span><span class="ic"></span>9:00 Am<span class="sep">|</span><span class="ic"></span>0 comments<span class="sep">|</span><span class="stars">★★★★☆</span><span class="reviews">(34 Reviews)</span></div>
  <div class="post-photo" role="img" aria-label="Silhouette pulling large letters that spell possible against a purple and orange sunset" style="background:linear-gradient(180deg,#5d5a8c 0%,#b07a8a 35%,#f0a45a 60%,#c77a3a 80%,#2a1c16 100%)"></div>
  <p class="post-excerpt">At vero eos et accusamus et iusto odio dignissimos ducimus qui blanditiis praesentium voluptatum dele niti atque corrupti quos dolores et quas molestias excepturi sint occaecati cupiditate non providentsimil ique sunt in culpa qui officia deserunt mollitia animi, id est laborum et dolorum fuga. Et harum quidem rerum facilis est et expedita distinctio. m soluta nobis est eligend.</p>
  <span class="btn-outline">READ MORE &gt;&gt;</span>
  <div class="share-row"><span>Like</span><span class="count">200</span><span>Share</span><span class="count">200</span><span>+1</span><span class="count">200</span></div>
</article>

<span class="view-more">VIEW MORE &gt;&gt;</span>

<aside class="sidebar">
  <section class="profile">
    <div class="avatar" role="img" aria-label="Portrait of the blog author"></div>
    <div class="profile-name">MAYA</div>
    <div class="profile-role">Finibus Bonorum et</div>
    <div class="profile-rule"></div>
    <p class="profile-bio">Nam libero tempore, cum soluta nobis est eligendioptio cumque nihil impedit quo minus id quod maximplaceat facere possimus, omnis voluptas assumenda est, omnis dolor repe us autem quibusdam etau</p>
    <div class="profile-social"><span></span><span></span><span></span><span></span><span></span></div>
  </section>

  <h3 class="widget-title" style="top:453px">Related Articles</h3>
  <div class="related-item" style="top:525px">
    <div class="related-thumb" role="img" aria-label="Darts in a dartboard" style="background:linear-gradient(90deg,#2a3a2e,#b33a2e,#2c2c2c)"></div>
    <div class="related-text">Sunt in culpa qui officia des erunt mollitia animi</div>
    <div class="related-date">15/03/2017</div>
  </div>
  <div class="related-item" style="top:637px">
    <div class="related-thumb" role="img" aria-label="Smiling woman in a light setting" style="background:linear-gradient(90deg,#f0e6dc,#e08a6a,#f2ece4)"></div>
    <div class="related-text">Sunt in culpa qui officia des erunt mollitia animi</div>
    <div class="related-date">15/03/2017</div>
  </div>
  <div class="related-item" style="top:749px">
    <div class="related-thumb" role="img" aria-label="Hand touching a glowing goals screen" style="background:linear-gradient(90deg,#1c2f5a,#3a6ab0,#dfe8f2)"></div>
    <div class="related-text">Sunt in culpa qui officia des erunt mollitia animi</div>
    <div class="related-date">15/03/2017</div>
  </div>
  <div class="related-item" style="top:861px">
    <div class="related-thumb" role="img" aria-label="Person standing on a beach under a pale sky" style="background:linear-gradient(180deg,#b9d3e3,#e6dcc6)"></div>
    <div class="related-text">Sunt in culpa qui officia des erunt mollitia animi</div>
    <div class="related-date">15/03/2017</div>
  </div>
  <span class="link-teal" style="top:990px">VIEW MORE &gt;&gt;</span>

  <section class="newsletter">
    <h3 class="widget-title" style="top:48px">Newsletter</h3>
    <div class="email-field">ENTER YOUR EMAIL ADDRESS</div>
    <div class="btn-solid">SIGN UP</div>
    <p class="newsletter-note">By signing up, you are opting in to receive periodic communications from Bright Path Notes</p>
  </section>

  <h3 class="widget-title" style="top:1390px">Join us on Friendbook</h3>
  <div class="fb-card" role="img" aria-label="Page banner showing a climber on a rock face">
    <div class="fb-brand">BRIGHT PATH NOTES</div>
    <div class="fb-name">Bright Path Notes</div>
    <div class="fb-likes">4,893 LIKES</div>
    <span class="fb-btn" style="left:12px">Like Page</span>
    <span class="fb-btn" style="right:12px">Sign Up</span>
  </div>
  <p class="fb-note">Be the first of your friends to like this</p>
  <div class="fb-friends">
    <span role="img" aria-label="Friend profile photo" style="background:#6a7a8a"></span>
    <span role="img" aria-label="Friend profile photo" style="background:#9aa4ae"></span>
    <span role="img" aria-label="Friend profile photo" style="background:#b08a6e"></span>
    <span role="img" aria-label="Friend profile photo" style="background:#c27a5a"></span>
    <span role="img" aria-label="Friend profile photo" style="background:#7f98b4"></span>
    <span role="img" aria-label="Friend profile photo" style="background:#5a4e48"></span>
    <span role="img" aria-label="Friend profile photo" style="background:#8c8076"></span>
  </div>
</aside>

<footer class="site-footer">
  <div class="footer-social"><span></span><span></span><span></span><span></span><span></span></div>
  <div class="footer-links">Home<span class="sep">|</span>About<span class="sep">|</span>Contact</div>
  <div class="copyright">Copyright © 2017, Bright Path Notes. All Rights Reserved.</div>
</footer>

</body>
</html>
```